Harbor Crestline (Business Card Design)

Need business cards designed. Something modern, chic, and sleek. Mabye the back of the card should be the navy blue that is in the logo and then just the logo on the back.

Target Market(s)

Those in the hotel, office, and renovation industry

Contact Information for Business Card

1. Logo 2. Dorian Fenwick 3. CEO/Founder 4. Phone: (833) HarbCre / (833) 427-2731 5. Email: dorian@theharborcrestline.com 6. Website: www.theharborcrestline.com

Font styles to use
Other font styles liked:
• Look at the logo font and base the font for everything else off of that.

Colors
0054AA
0677BA
7BADD7
CADEEF
E8F1F8

Requirements
Must have
• Colors that are associated in the logo
Nice to have
• Sleek modern clean and chic design.

```html
<!DOCTYPE html>
<html lang="en">
<head>
<meta charset="utf-8">
<title>Harbor Crestline — Business Card</title>
<link rel="stylesheet" href="https://fonts.googleapis.com/css2?family=Montserrat:wght@500;700;800&family=Open+Sans:wght@400;600&display=swap">
<style>
  :root {
    --stage: #1c1c1e;
    --navy: #0d1a4d;
    --navy-deep: #0a1238;
    --navy-light: #25307a;
    --gold: #c9a044;
    --white: #ffffff;
    --card-w: 560px;
    --card-h: 320px;
  }
  * { box-sizing: border-box; margin: 0; padding: 0; }
  html, body { width: 1200px; height: 780px; overflow: hidden; }
  body {
    background: var(--stage);
    display: flex;
    align-items: center;
    justify-content: center;
    gap: 32px;
    font-family: "Open Sans", Arial, sans-serif;
  }
  .card {
    position: relative;
    width: var(--card-w);
    height: var(--card-h);
    border-radius: 22px;
    border: 2px solid var(--gold);
    background: var(--navy);
    overflow: hidden;
  }

  /* Back side */
  .card-back__pattern {
    position: absolute;
    inset: 0;
    background: linear-gradient(160deg, var(--navy-light) 0%, #141d5c 40%, var(--navy-deep) 100%);
  }
  .card-back__brand {
    position: absolute;
    right: 34px;
    bottom: 30px;
    display: flex;
    align-items: center;
    gap: 8px;
    font-family: "Montserrat", Arial, sans-serif;
    font-weight: 700;
    font-size: 13px;
    letter-spacing: 1.5px;
    text-transform: uppercase;
    color: var(--white);
  }
  .brand-square {
    width: 12px;
    height: 12px;
    background: var(--white);
  }

  /* Front side */
  .card-front__tab {
    position: absolute;
    top: 0;
    right: 44px;
    width: 16px;
    height: 58px;
    background: var(--gold);
  }
  .card-front__identity {
    position: absolute;
    top: 22px;
    right: 74px;
    text-align: right;
  }
  .person-name {
    font-family: "Montserrat", Arial, sans-serif;
    font-weight: 800;
    font-size: 29px;
    line-height: 1.05;
    color: var(--gold);
  }
  .person-name__last { color: var(--white); }
  .person-title {
    font-family: "Montserrat", Arial, sans-serif;
    font-weight: 500;
    font-size: 13px;
    color: var(--white);
    margin-top: 3px;
  }
  .card-front__emboss {
    position: absolute;
    right: 48px;
    top: 104px;
    width: 134px;
    height: 134px;
    background: linear-gradient(180deg, #4b4f9a 0%, #1b2566 45%, var(--navy-deep) 100%);
  }
  .card-front__brand {
    position: absolute;
    left: 36px;
    top: 122px;
    display: flex;
    align-items: center;
    gap: 10px;
    font-family: "Montserrat", Arial, sans-serif;
    font-weight: 700;
    font-size: 21px;
    letter-spacing: 2px;
    text-transform: uppercase;
    color: var(--white);
  }
  .card-front__brand .brand-square {
    width: 16px;
    height: 16px;
    background: var(--gold);
  }
  .address {
    position: absolute;
    left: 36px;
    top: 170px;
    font-size: 13.5px;
    line-height: 1.4;
    color: var(--white);
  }
  .contact-list {
    position: absolute;
    left: 36px;
    top: 222px;
    list-style: none;
  }
  .contact-list li {
    display: flex;
    align-items: center;
    gap: 9px;
    font-size: 13.5px;
    line-height: 1.6;
    color: var(--white);
  }
  .contact-list svg {
    width: 13px;
    height: 13px;
    flex: none;
  }
</style>
</head>
<body>

  <section class="card card-back" aria-label="Card back">
    <div class="card-back__pattern" role="img" aria-label="Repeating brand pattern fading from light to deep navy"></div>
    <div class="card-back__brand"><span class="brand-square"></span>Harbor Crestline</div>
  </section>

  <section class="card card-front" aria-label="Card front">
    <div class="card-front__tab"></div>
    <div class="card-front__identity">
      <p class="person-name">Dorian <span class="person-name__last">Fenwick</span></p>
      <p class="person-title">CEO/Founder</p>
    </div>
    <div class="card-front__emboss" role="img" aria-label="Large embossed brand mark area"></div>

    <div class="card-front__brand"><span class="brand-square"></span>Harbor Crestline</div>

    <p class="address">4120 Larkmoor Ave<br>Suite 2100, Brenton, MD 21990</p>

    <ul class="contact-list">
      <li>
        <svg viewBox="0 0 24 24" aria-hidden="true"><path fill="#c9a044" d="M6.6 10.8a15.1 15.1 0 0 0 6.6 6.6l2.2-2.2a1 1 0 0 1 1-.25 11.4 11.4 0 0 0 3.6.57 1 1 0 0 1 1 1V20a1 1 0 0 1-1 1A17 17 0 0 1 3 4a1 1 0 0 1 1-1h3.5a1 1 0 0 1 1 1c0 1.25.2 2.45.57 3.6a1 1 0 0 1-.25 1z"/></svg>
        (833) HarbCre / (833) 427-2731
      </li>
      <li>
        <svg viewBox="0 0 24 24" aria-hidden="true"><g fill="none" stroke="#c9a044" stroke-width="2"><circle cx="12" cy="12" r="9"/><path d="M3 12h18M12 3c3 3.2 3 14.8 0 18M12 3c-3 3.2-3 14.8 0 18"/></g></svg>
        www.theharborcrestline.com
      </li>
      <li>
        <svg viewBox="0 0 24 24" aria-hidden="true"><g fill="none" stroke="#c9a044" stroke-width="2"><rect x="3" y="5" width="18" height="14" rx="1"/><path d="M3 6l9 7 9-7"/></g></svg>
        dorian@theharborcrestline.com
      </li>
    </ul>
  </section>

</body>
</html>
```